Ancient Art and Artifact information website

Hello Designers,
We are starting up a new website who talk abut and discusses an ancient arts artifacts. We would covering a wide range of countries ranging from Egypt, Greece, India, Syria, Rome, etc. My website name Bright Loom
Designs that fits with ancient theme and some kind of uniqueness would be accepted.
Requirements:
1) A home page design
2) Sub page design
3) A suitable logo
Sections can be added are featured ancient arts/places with short description followed by a more button, latest news, and comment section.
Add contents if you found relevant for this category of website. Ability to share the information through social media is desired.
Must be a responsive design. I look forward to designs which are mind blowing.
Number of Pages Required
2 page

```html
<!DOCTYPE html>
<html lang="en">
<head>
<meta charset="utf-8">
<title>Bright Loom — Ancient Arts Artifacts</title>
<link href="https://fonts.googleapis.com/css2?family=Open+Sans:ital,wght@0,300;0,400;0,600;0,700;0,800;1,400&display=swap" rel="stylesheet">
<style>
:root{
  --accent:#a45f48;
  --band:#a8624c;
  --button:#b27b67;
  --ink:#333333;
  --muted:#777777;
  --light:#f4f4f4;
  --line:#e2e2e2;
  --white:#ffffff;
}
*{margin:0;padding:0;box-sizing:border-box}
html,body{width:1200px;height:2727px;overflow:hidden}
body{position:relative;font-family:"Open Sans",Arial,sans-serif;color:var(--ink);background:var(--white)}
.abs{position:absolute}
.center{left:0;width:1200px;text-align:center}

/* header */
.site-header{top:0;left:0;width:1200px;height:113px;background:var(--white)}
.brand{left:100px;top:42px;font-size:30px;font-weight:400;letter-spacing:1px;color:var(--accent);text-transform:uppercase}
.nav{top:47px;right:98px;display:flex;gap:0;list-style:none}
.nav li{height:29px;line-height:29px;font-size:13.5px;padding:0 15px;text-transform:uppercase;color:var(--ink)}
.nav li.active{background:var(--accent);color:var(--white);padding:0 20px;margin-right:8px}

/* hero */
.hero{top:113px;left:0;width:1200px;height:536px;background:linear-gradient(180deg,#2f5a8f 0%,#4a6d94 35%,#6f6a62 62%,#4c4036 100%)}
.hero-title{top:270px;font-size:66px;font-weight:800;color:var(--white);letter-spacing:1px}
.hero-text{top:358px;left:190px;width:820px;text-align:center;font-size:16px;line-height:23px;color:var(--white)}
.btn-light{top:447px;left:504px;width:192px;height:40px;background:var(--white);color:#222;font-size:16px;font-weight:600;text-align:center;line-height:40px;text-transform:uppercase}
.hero-arrow{top:307px;width:44px;height:44px;border-radius:50%;background:rgba(255,255,255,.12)}
.hero-arrow svg{display:block}

/* welcome */
.section-title{font-size:33px;font-weight:300;text-transform:uppercase;color:var(--ink)}
.section-title span{color:var(--accent)}
.welcome-title{top:712px}
.rule{top:768px;left:510px;width:180px;height:1px;background:var(--line)}
.welcome-text{top:786px;left:110px;width:980px;text-align:center;font-size:14px;line-height:29px;color:var(--muted)}
.btn-accent{top:914px;left:518px;width:164px;height:40px;background:var(--button);color:var(--white);font-size:16px;font-weight:600;text-align:center;line-height:40px;text-transform:uppercase}

/* featured */
.featured{top:1020px;left:0;width:1200px;height:613px;background:var(--band)}
.featured-title{top:1066px;color:var(--white)}
.featured-text{top:1122px;left:140px;width:920px;text-align:center;font-size:14.5px;line-height:29px;color:#f3e5df}
.mini-arrow{top:1183px;width:25px;height:24px;border:1px solid #e9d3ca}
.card-img{top:1225px;width:307px;height:162px}
.card-title{top:1402px;width:307px;text-align:center;font-size:27px;font-weight:400;color:var(--white);text-transform:uppercase}
.card-text{top:1446px;width:307px;text-align:center;font-size:12.5px;line-height:20px;color:#ecd3c9}
.btn-outline{top:1525px;width:169px;height:40px;border:1px solid #e7cbc0;color:var(--white);font-size:16px;text-align:center;line-height:38px;text-transform:uppercase}

/* news */
.news-title{top:1680px}
.news-img{top:1785px;width:307px;height:158px}
.news-heading{top:1960px;font-size:20px;color:var(--ink)}
.news-text{top:1992px;width:300px;font-size:12.5px;line-height:21px;color:#444}
.news-date{top:2042px;font-size:17px;color:#333}

/* comments */
.comments{top:2142px;left:0;width:1200px;height:503px;background:var(--light)}
.comments-title{top:2190px;left:478px;display:flex;align-items:center;gap:6px;font-size:33px;font-weight:300;text-transform:uppercase}
.avatar{width:100px;height:100px;border-radius:50%;background:radial-gradient(circle at 50% 40%,#d9d9d9,#9c9c9c)}
.comment-name{font-size:18px;font-weight:400;text-transform:uppercase;color:#222;left:227px}
.comment-date{font-size:12px;font-style:italic;text-transform:uppercase;color:#444;left:227px}
.comment-text{left:227px;width:880px;font-size:12.5px;line-height:24px;color:#666}
.reply{left:1023px;width:77px;height:27px;background:#e5e5e5;font-size:12px;font-style:italic;text-align:center;line-height:27px;color:#333}
.divider{top:2429px;left:100px;width:1000px;height:1px;background:#dddddd}

/* footer */
.site-footer{top:2645px;left:0;width:1200px;height:82px;background:var(--white)}
.copyright{top:2677px;left:100px;font-size:11px;color:#444}
.social-label{top:2677px;left:750px;font-size:11px;color:#444}
.social{top:2670px;width:30px;height:30px;border-radius:50%}
</style>
</head>
<body>

<header class="abs site-header">
  <div class="abs brand">Bright Loom</div>
  <ul class="abs nav">
    <li class="active">Home</li>
    <li>Ancient Arts/Places</li>
    <li>Latest News</li>
    <li>Comments</li>
    <li>Contact Us</li>
  </ul>
</header>

<section>
  <div class="abs hero" role="img" aria-label="Photograph of ancient stone ruins with carved columns under a blue sky"></div>
  <h1 class="abs center hero-title">ANCIENT ARTS ARTIFACTS</h1>
  <p class="abs hero-text">Sed ut perspiciatis unde omnis iste natus error sit voluptatem accusantium doloremque laudantium, totam rem aperiam eaque ipsa quae ab illo inventore veritatis et quasi</p>
  <div class="abs btn-light">Get Started</div>
  <div class="abs hero-arrow" style="left:29px"><svg width="44" height="44"><path d="M25 13 L16 22 L25 31" fill="none" stroke="#fff" stroke-width="1.5"/></svg></div>
  <div class="abs hero-arrow" style="left:1120px"><svg width="44" height="44"><path d="M19 13 L28 22 L19 31" fill="none" stroke="#fff" stroke-width="1.5"/></svg></div>
</section>

<section>
  <h2 class="abs center section-title welcome-title">Welcome to <span>Bright Loom</span></h2>
  <div class="abs rule"></div>
  <p class="abs welcome-text">Sed ut perspiciatis unde omnis iste natus error sit voluptatem accusantium doloremque laudantium, totam rem aperiam, eaque ipsa quae ab illo inventore veritatis et quasi architecto beatae vitae dicta sunt explicabo. Nemo enim ipsam voluptatem quia voluptas sit aspernatur aut odit aut fugit, sed quia consequuntur magni dolores eos qui ratione voluptatem sequi nesciunt.</p>
  <div class="abs btn-accent">Read More</div>
</section>

<section>
  <div class="abs featured"></div>
  <h2 class="abs center section-title featured-title">Featured Ancient Arts/Places</h2>
  <p class="abs featured-text">But I must explain to you how all this mistaken idea of denouncing pleasure and praising pain was born and I will give you a complete account of the system, and expound the actual teachings of the great explorer of the truth.</p>
  <div class="abs mini-arrow" style="left:1045px"><svg width="23" height="22"><path d="M13 6 L8 11 L13 16" fill="none" stroke="#fff" stroke-width="1.4"/></svg></div>
  <div class="abs mini-arrow" style="left:1075px"><svg width="23" height="22"><path d="M10 6 L15 11 L10 16" fill="none" stroke="#fff" stroke-width="1.4"/></svg></div>

  <div class="abs card-img" style="left:100px;background:linear-gradient(180deg,#e0a14a 0%,#b8622a 45%,#3a2a22 100%)" role="img" aria-label="Photograph of an ancient temple at sunset"></div>
  <h3 class="abs card-title" style="left:100px">Egypt</h3>
  <p class="abs card-text" style="left:100px">Lorem ipsum dolor sit amet, consectetur adipiscing elit, sed do eiusmod tempor incididunt ut labore et dolore magna aliqua.</p>
  <div class="abs btn-outline" style="left:169px">Read More</div>

  <div class="abs card-img" style="left:445px;background:linear-gradient(180deg,#4f86c2 0%,#9fb3c4 50%,#8a8a85 100%)" role="img" aria-label="Photograph of a columned Greek temple on a rocky hill"></div>
  <h3 class="abs card-title" style="left:445px">Greece</h3>
  <p class="abs card-text" style="left:445px">Lorem ipsum dolor sit amet, consectetur adipiscing elit, sed do eiusmod tempor incididunt ut labore et dolore magna aliqua.</p>
  <div class="abs btn-outline" style="left:514px">Read More</div>

  <div class="abs card-img" style="left:793px;background:linear-gradient(180deg,#b9d3e6 0%,#b9795a 45%,#4f7a3c 100%)" role="img" aria-label="Photograph of a domed red stone monument with gardens"></div>
  <h3 class="abs card-title" style="left:793px">Rome</h3>
  <p class="abs card-text" style="left:793px">Lorem ipsum dolor sit amet, consectetur adipiscing elit, sed do eiusmod tempor incididunt ut labore et dolore magna aliqua.</p>
  <div class="abs btn-outline" style="left:862px">Read More</div>
</section>

<section>
  <h2 class="abs center section-title news-title">Latest News</h2>

  <div class="abs news-img" style="left:100px;background:linear-gradient(180deg,#5d8fc9 0%,#5b6a3e 50%,#8c7a5e 100%)" role="img" aria-label="Photograph of an ancient theatre ruin among trees"></div>
  <h3 class="abs news-heading" style="left:105px;font-weight:400">Latest News title name</h3>
  <p class="abs news-text" style="left:105px">Class aptent taciti sociosqu ad litora torquent per co nubia nostra per inceptos hymenaeos</p>
  <div class="abs news-date" style="left:107px">25 FEB 2016</div>

  <div class="abs news-img" style="left:447px;background:linear-gradient(135deg,#c9b48e 0%,#8f7c62 55%,#d7c7a6 100%)" role="img" aria-label="Photograph of a weathered stone sculpture"></div>
  <h3 class="abs news-heading" style="left:452px;font-weight:400">Latest News title name</h3>
  <p class="abs news-text" style="left:452px">Class aptent taciti sociosqu ad litora torquent per co nubia nostra per inceptos hymenaeos</p>
  <div class="abs news-date" style="left:454px">25 FEB 2016</div>

  <div class="abs news-img" style="left:793px;background:linear-gradient(180deg,#3f6fb5 0%,#8fa9cf 40%,#c89a55 65%,#d9b77a 100%)" role="img" aria-label="Photograph of pyramids in the desert"></div>
  <h3 class="abs news-heading" style="left:798px;font-weight:400">Latest News title name</h3>
  <p class="abs news-text" style="left:798px">Class aptent taciti sociosqu ad litora torquent per co nubia nostra per inceptos hymenaeos</p>
  <div class="abs news-date" style="left:801px">25 FEB 2016</div>
</section>

<section>
  <div class="abs comments"></div>
  <h2 class="abs comments-title">
    <svg width="54" height="46" viewBox="0 0 54 46"><path d="M4 3 H50 V33 H24 L14 43 V33 H4 Z" fill="none" stroke="var(--accent)" stroke-width="3" stroke-linejoin="round"/></svg>
    Comments
  </h2>

  <div class="abs avatar" style="left:100px;top:2274px" role="img" aria-label="Commenter portrait"></div>
  <div class="abs comment-name" style="top:2286px">Quis Nostrum</div>
  <div class="abs comment-date" style="top:2317px">February 1, 2017 at 11:18 PM</div>
  <p class="abs comment-text" style="top:2346px">Lorem ipsum dolor sit amet, consectetur adipiscing elit, sed do eiusmod tempor incididunt ut labore et dolore magna aliqua. Ut enim ad minim veniam, quis nostrud exercitation ullamco laboris nisi ut aliquip ex ea commodo consequat.</p>
  <div class="abs reply" style="top:2291px">Reply</div>

  <div class="abs divider"></div>

  <div class="abs avatar" style="left:100px;top:2454px" role="img" aria-label="Commenter portrait"></div>
  <div class="abs comment-name" style="top:2466px">Adipisci Velit</div>
  <div class="abs comment-date" style="top:2497px">February 8, 2017 at 10:18 PM</div>
  <p class="abs comment-text" style="top:2526px">Lorem ipsum dolor sit amet, consectetur adipiscing elit, sed do eiusmod tempor incididunt ut labore et dolore magna aliqua. Ut enim ad minim veniam, quis nostrud exercitation ullamco laboris nisi ut aliquip ex ea commodo consequat.</p>
  <div class="abs reply" style="top:2471px">Reply</div>
</section>

<footer class="abs site-footer">
</footer>
<div class="abs copyright">© 2017. Bright Loom. All rights reserved.</div>
<div class="abs social-label">Connect with our social network :</div>
<div class="abs social" style="left:930px;background:#2f62a8"></div>
<div class="abs social" style="left:966px;background:#2a77a8"></div>
<div class="abs social" style="left:1002px;background:#e8a43a"></div>
<div class="abs social" style="left:1038px;background:#45aee0"></div>
<div class="abs social" style="left:1074px;background:#d9332b"></div>

</body>
</html>
```